Business Card Design

I already have a company logo for my company. I have a logo for the manufacturer we represent. I want a professional business card design.

```html
<!DOCTYPE html>
<html lang="en">
<head>
<meta charset="utf-8">
<title>Harbor Signal Co – Business Cards</title>
<link rel="stylesheet" href="https://fonts.googleapis.com/css2?family=Open+Sans:wght@400;600;700&display=swap">
<style>
  :root {
    --stage: #3a3a3a;
    --card-white: #ffffff;
    --card-black: #050505;
    --brand-red: #e31e26;
    --brand-gold: #e0a928;
    --text-grey: #3c3c3c;
    --text-light: #f2f2f2;
  }
  * { margin: 0; padding: 0; box-sizing: border-box; }
  html, body {
    width: 1200px; height: 780px; overflow: hidden;
    background: var(--stage);
    font-family: "Open Sans", Arial, sans-serif;
  }
  .stage {
    width: 1200px; height: 780px;
    display: flex; align-items: center; justify-content: center; gap: 50px;
  }
  .card {
    position: relative;
    width: 525px; height: 300px;
    border-radius: 18px;
    overflow: hidden;
  }
  .card--front { background: var(--card-white); }
  .card--back { background: var(--card-black); display: flex; align-items: center; justify-content: center; }

  .card__wave { position: absolute; inset: 0; width: 100%; height: 100%; }

  .brand {
    position: absolute; display: flex; align-items: center; gap: 10px;
    font-weight: 700; text-transform: uppercase; letter-spacing: 1px; line-height: 1.05;
  }
  .brand__mark { width: 16px; height: 16px; background: var(--brand-red); flex: none; }
  .card--front .brand { left: 34px; top: 46px; font-size: 24px; color: var(--brand-red); }
  .card--back .brand { position: static; font-size: 38px; color: var(--text-light); }
  .card--back .brand__mark { width: 26px; height: 26px; }

  .edge-tab {
    position: absolute; right: 0; top: 60px;
    width: 10px; height: 34px; background: var(--brand-red);
  }

  .person { position: absolute; right: 42px; top: 58px; text-align: right; }
  .person__name {
    font-size: 22px; font-weight: 700; color: var(--brand-red);
    text-transform: uppercase; letter-spacing: 0.5px;
  }
  .person__role { font-size: 13px; color: var(--text-grey); margin-top: 2px; }

  .contact {
    position: absolute; right: 22px; top: 186px;
    list-style: none; text-align: right;
    color: var(--text-light); font-size: 12.5px; line-height: 17px;
  }
  .contact__item { display: flex; justify-content: flex-end; align-items: center; gap: 8px; }
  .contact__icon { width: 12px; height: 12px; flex: none; }
  .contact__spacer { width: 12px; flex: none; }
  .contact__gap { margin-top: 6px; }
</style>
</head>
<body>
<main class="stage">

  <section class="card card--front" aria-label="Business card front">
    <svg class="card__wave" viewBox="0 0 525 300" aria-hidden="true">
      <path d="M0,236 C70,196 150,176 240,170 C350,162 470,160 525,120 L525,300 L0,300 Z" fill="var(--card-black)"/>
      <path d="M0,220 C70,182 150,162 240,156 C350,148 470,146 525,106" fill="none" stroke="var(--brand-red)" stroke-width="7"/>
      <path d="M0,196 C60,176 140,166 236,163" fill="none" stroke="var(--brand-gold)" stroke-width="5"/>
    </svg>

    <div class="brand">
      <span class="brand__mark"></span>
      <span class="brand__name">Harbor Signal<br>Co</span>
    </div>

    <div class="edge-tab"></div>

    <div class="person">
      <p class="person__name">Daniel Reyes</p>
      <p class="person__role">Managing Director</p>
    </div>

    <ul class="contact">
      <li class="contact__item">Your address, City<span class="contact__spacer"></span></li>
      <li class="contact__item">State, Zip 1234<span class="contact__spacer"></span></li>
      <li class="contact__item contact__gap">123 456 789
        <svg class="contact__icon" viewBox="0 0 24 24" aria-hidden="true"><path fill="var(--brand-red)" d="M6.6 10.8a15.1 15.1 0 0 0 6.6 6.6l2.2-2.2a1 1 0 0 1 1-.25 11.4 11.4 0 0 0 3.6.6 1 1 0 0 1 1 1V20a1 1 0 0 1-1 1A17 17 0 0 1 3 4a1 1 0 0 1 1-1h3.5a1 1 0 0 1 1 1c0 1.25.2 2.45.6 3.6a1 1 0 0 1-.25 1z"/></svg>
      </li>
      <li class="contact__item">info@yourmail.com
        <svg class="contact__icon" viewBox="0 0 24 24" aria-hidden="true"><rect x="2" y="5" width="20" height="14" rx="2" fill="var(--brand-red)"/><path d="M3 6l9 7 9-7" fill="none" stroke="var(--card-black)" stroke-width="2"/></svg>
      </li>
      <li class="contact__item">www.yourwebsite.com
        <svg class="contact__icon" viewBox="0 0 24 24" aria-hidden="true"><circle cx="12" cy="12" r="10" fill="var(--brand-red)"/><path d="M2 12h20M12 2c3 3 3 17 0 20M12 2c-3 3-3 17 0 20" fill="none" stroke="var(--card-black)" stroke-width="1.5"/></svg>
      </li>
    </ul>
  </section>

  <section class="card card--back" aria-label="Business card back">
    <div class="brand">
      <span class="brand__mark"></span>
      <span class="brand__name">Harbor Signal Co</span>
    </div>
  </section>

</main>
</body>
</html>
```